Website 950x200 Header w/ logo

I'm in need of a website header for a new site called DaysofMarlo.com

The site is basically a glorified blog for myself to write my thoughts about politics, sports, TV shows, current events, whatever. I have a lot of interests.

The site is going to look very very similar to http://www.brisknetmaker.example/4093817/8-ways-to-win-the-race-for-creative-talent

but instead of having a dynamic header that becomes the picture with each article, its just going to be a static header in which I'd like to have the name of the site (Days of Marlo) and some kind of logo, pictures, etc - I'm totally open to anything. The only thing is it needs to have a dark (probably black) background and needs to be 950x200px.

I envision a black background, with gray and white as the primary colors and then some secondary colors potentially, but again I'm open to anything as long as it's on the black background or some kind of charcoal gray or wahtever. On the site the black part will go all the way from the left of the screen to the right no matter what the window size, but I'd like to keep all the content inside of 950x200px

email me marlo.pettigrew@inboxly.example if you have any questions. Thanks!

Industry/Entity Type

Tv

```html
<!DOCTYPE html>
<html lang="en">
<head>
<meta charset="utf-8">
<title>Days of Marlo – Header</title>
<link rel="stylesheet" href="https://fonts.googleapis.com/css2?family=Tinos&display=swap">
<style>
  :root {
    --page: #ffffff;
    --band: #333333;
    --ink: #ffffff;
    --ink-faint: rgba(255,255,255,0.12);
    --paper: #e9e9e6;
    --paper-dark: #b9b9b4;
    --globe-a: #c94a4a;
    --globe-b: #2c4a8a;
    --sport: #c92b2b;
    --tv-dark: #111111;
  }
  html, body {
    margin: 0;
    padding: 0;
    overflow: hidden;
    background: var(--page);
  }
  .canvas {
    position: relative;
    width: 1200px;
    height: 333px;
    background: var(--page);
    overflow: hidden;
    font-family: "Tinos", "Times New Roman", serif;
  }
  .header-band {
    position: absolute;
    left: 0;
    top: 23px;
    width: 1200px;
    height: 266px;
    background: var(--band);
    overflow: hidden;
  }
  .dot-field {
    position: absolute;
    left: 200px;
    top: 60px;
    width: 920px;
    height: 210px;
    background: radial-gradient(ellipse at 50% 50%, rgba(140,140,140,0.28) 0%, rgba(140,140,140,0.12) 45%, rgba(51,51,51,0) 75%);
  }
  .brand-mark {
    position: absolute;
    left: 30px;
    top: 41px;
    margin: 0;
    font-size: 128px;
    line-height: 1;
    font-weight: 400;
    color: var(--ink);
    letter-spacing: 1px;
  }
  .brand-url {
    position: absolute;
    left: 20px;
    top: 165px;
    margin: 0;
    font-size: 34px;
    line-height: 1;
    color: var(--ink);
  }
  .brand-url-echo {
    position: absolute;
    left: 36px;
    top: 196px;
    margin: 0;
    font-size: 34px;
    line-height: 1;
    color: var(--ink-faint);
    transform: scaleY(0.7);
    transform-origin: top left;
    filter: blur(1.2px);
  }
  .site-title {
    position: absolute;
    left: 0;
    width: 1200px;
    top: 154px;
    margin: 0;
    text-align: center;
    font-size: 54px;
    line-height: 1;
    font-weight: 400;
    color: var(--ink);
  }
  .art {
    position: absolute;
  }
  .art-news {
    left: 763px;
    top: 40px;
    width: 110px;
    height: 108px;
    background: linear-gradient(160deg, var(--paper) 0%, var(--paper-dark) 100%);
    border-radius: 10px 4px 16px 6px;
    transform: rotate(-12deg);
  }
  .art-sport {
    left: 963px;
    top: 42px;
    width: 154px;
    height: 44px;
    background: linear-gradient(90deg, #eeeeee 0%, #eeeeee 30%, var(--sport) 42%, var(--sport) 58%, #eeeeee 70%);
    border-radius: 4px;
    opacity: 0.9;
  }
  .art-globe {
    left: 862px;
    top: 152px;
    width: 118px;
    height: 118px;
    border-radius: 50%;
    background: radial-gradient(circle at 38% 35%, #f2f2f2 0%, var(--globe-a) 45%, var(--globe-b) 100%);
  }
  .tv-badge {
    position: absolute;
    left: 1050px;
    top: 131px;
    width: 104px;
    height: 108px;
    background: var(--tv-dark);
    display: flex;
    align-items: center;
    justify-content: center;
  }
  .tv-badge span {
    font-size: 18px;
    color: var(--ink);
    font-weight: 400;
  }
</style>
</head>
<body>
  <div class="canvas">
    <div class="header-band"></div>
    <div class="dot-field" role="img" aria-label="Scattered grey oval dots decorating the dark band"></div>

    <p class="brand-mark">DoM</p>
    <p class="brand-url">DaysofMarlo.com</p>
    <p class="brand-url-echo" aria-hidden="true">DaysofMarlo.com</p>

    <h1 class="site-title">Days of Marlo</h1>

    <div class="art art-news" role="img" aria-label="Illustration of a rolled newspaper with a news headline"></div>
    <div class="art art-sport" role="img" aria-label="Decorative sport lettering graphic"></div>
    <div class="art art-globe" role="img" aria-label="Globe covered in newspaper front pages"></div>
    <div class="tv-badge"><span>TuneVision</span></div>
  </div>
</body>
</html>
```